Business Recognition Design

We need a design for a recognition to be given to business leaders in our community.
The recognition shall be made on a brass plaque on wood panel background (picture attached, please use it as a background), and all drawing must be in vectors and only one color (black).
It should also have a logo on the top and signature on the right bottom.
The text is enclosed in DOC file.
Updates

Reason: just to be able to find the best solution

Reason: None of the suggestion is good enough. Logo in general is too big in comparison with the rest of the plate.

Industry/Entity Type

Business

Requirements
Must have
• - standard Windows font (or possibility to install the same font on Windows), as the name on the recognition shall be printed in the same font
Nice to have
• - some graphic element (in curves) representing achievements in business
- should look great :)

```html
<!DOCTYPE html>
<html lang="en">
<head>
<meta charset="utf-8">
<title>Business Recognition Plaque</title>
<link href="https://fonts.googleapis.com/css2?family=Arimo:wght@400;700&family=Didact+Gothic&family=Almendra:wght@400;700&display=swap" rel="stylesheet">
<style>
  :root {
    --wall-dark: #b78560;
    --wall: #c99a72;
    --wall-light: #dcb48e;
    --wood-dark: #4a2a17;
    --wood: #6e4327;
    --wood-light: #8a5634;
    --brass-dark: #c9a227;
    --brass: #e9cf6a;
    --brass-light: #f6e79c;
    --ink: #262218;
    --ribbon-light: #ffc23a;
    --ribbon: #f2a21c;
    --ribbon-dark: #d77a14;
  }
  html, body {
    margin: 0;
    padding: 0;
    width: 1200px;
    height: 973px;
    overflow: hidden;
  }
  .canvas {
    position: relative;
    width: 1200px;
    height: 973px;
    overflow: hidden;
  }
  .wallpaper {
    position: absolute;
    inset: 0;
    background:
      radial-gradient(ellipse at 30% 20%, var(--wall-light), transparent 60%),
      radial-gradient(ellipse at 75% 80%, var(--wall-light), transparent 55%),
      linear-gradient(135deg, var(--wall) 0%, var(--wall-dark) 50%, var(--wall) 100%);
  }
  .plaque-art {
    position: absolute;
    inset: 0;
  }
  .ribbon-banner {
    position: absolute;
    left: 326px;
    top: 248px;
    width: 574px;
    height: 150px;
    border-radius: 18px;
    background: linear-gradient(90deg, var(--ribbon) 0%, var(--ribbon-light) 50%, var(--ribbon-dark) 100%);
  }
  .text {
    position: absolute;
    margin: 0;
    color: var(--ink);
    font-family: "Arimo", Arial, sans-serif;
    white-space: nowrap;
    line-height: 1;
  }
  .centered {
    transform: translateX(-50%);
    text-align: center;
  }
  .logo-name {
    left: 596px;
    top: 176px;
    font-family: "Didact Gothic", "Century Gothic", sans-serif;
    font-size: 48px;
  }
  .ribbon-title {
    left: 613px;
    top: 327px;
    font-family: "Almendra", Georgia, serif;
    font-size: 66px;
    color: #111;
    letter-spacing: 1px;
  }
  .award-title {
    left: 631px;
    top: 420px;
    font-size: 50px;
    font-weight: 700;
  }
  .award-to {
    left: 631px;
    top: 493px;
    font-size: 32px;
  }
  .recipient {
    left: 632px;
    top: 552px;
    font-size: 26px;
  }
  .citation {
    left: 600px;
    top: 611px;
    font-size: 27px;
    line-height: 51px;
  }
  .citation strong { font-weight: 700; }
  .date {
    left: 166px;
    top: 829px;
    font-size: 25px;
  }
  .signatory {
    left: 968px;
    top: 829px;
    font-size: 25px;
  }
</style>
</head>
<body>
<div class="canvas">
  <div class="wallpaper" role="img" aria-label="Ornate damask wallpaper backdrop in warm tan tones"></div>

  <svg class="plaque-art" width="1200" height="973" viewBox="0 0 1200 973" aria-hidden="true">
    <defs>
      <linearGradient id="wood" x1="0" y1="0" x2="1" y2="1">
        <stop offset="0" stop-color="var(--wood-light)"/>
        <stop offset="0.5" stop-color="var(--wood)"/>
        <stop offset="1" stop-color="var(--wood-dark)"/>
      </linearGradient>
      <linearGradient id="brass" x1="0" y1="0" x2="1" y2="1">
        <stop offset="0" stop-color="var(--brass-dark)"/>
        <stop offset="0.45" stop-color="var(--brass-light)"/>
        <stop offset="1" stop-color="var(--brass)"/>
      </linearGradient>
      <radialGradient id="screw" cx="0.35" cy="0.35" r="0.7">
        <stop offset="0" stop-color="#fff3b0"/>
        <stop offset="0.6" stop-color="#b8901e"/>
        <stop offset="1" stop-color="#5e430c"/>
      </radialGradient>
    </defs>

    <rect class="wood-panel" x="24" y="38" width="1154" height="894" fill="url(#wood)"/>
    <rect x="38" y="52" width="1126" height="866" fill="none" stroke="#3a1f10" stroke-width="2" opacity="0.6"/>

    <rect class="brass-plate" x="67" y="86" width="1063" height="795" fill="url(#brass)" stroke="#a88318" stroke-width="3"/>

    <circle cx="105" cy="119" r="14" fill="url(#screw)"/>
    <circle cx="1105" cy="119" r="14" fill="url(#screw)"/>
    <circle cx="105" cy="845" r="14" fill="url(#screw)"/>
    <circle cx="1105" cy="845" r="14" fill="url(#screw)"/>

    <line x1="897" y1="824" x2="1032" y2="824" stroke="var(--ink)" stroke-width="1.5"/>
  </svg>

  <div class="ribbon-banner" role="img" aria-label="Curled orange ribbon banner with maroon folds"></div>

  <p class="text centered logo-name">(Our Logo)</p>
  <p class="text centered ribbon-title">RECOGNITION</p>
  <h1 class="text centered award-title">The Best Entrepreneur in 2013</h1>
  <p class="text centered award-to">to</p>
  <p class="text centered recipient">Mr. Daniel R. Whitfield, MBA</p>
  <p class="text centered citation">
    Under the leadership of <strong>Mr. Daniel R. Whitfield</strong>, <strong>MBA</strong><br>
    the company <strong>DR-WHITFIELD Ltd</strong> has been selected<br>
    by a City Council as the best company of The City.
  </p>
  <p class="text date">Date: 4th July, 2013</p>
  <p class="text centered signatory">City Mayor</p>
</div>
</body>
</html>
```